Redesign of business card for Cedar Ridge Mechanical

We are looking for a new design for our business cards for Cedar Ridge Mechanical. We are a plumbing & HVAC construction company, operating on the West Coast of Canada and USA. Logo attached.
Industry/Entity Type
Construction - Plumbing & HVAC
Contact Information for Business Card
Name, address, phone numbers, email, website address
Look and feel
Each slider illustrates characteristics of the customer's brand and the style your logo design should communicate.

```html
<!DOCTYPE html>
<html lang="en">
<head>
<meta charset="utf-8">
<title>Cedar Ridge Mechanical – Business Card</title>
<link rel="stylesheet" href="https://fonts.googleapis.com/css2?family=Bebas+Neue&family=Montserrat:wght@400;700&display=swap">
<style>
  :root {
    --backdrop: #e6e2dc;
    --card-front: #ffffff;
    --card-back: #1b1b1b;
    --ink: #1e1e1e;
    --ink-soft: #2b2b2b;
    --back-mark: #4a4a4a;
  }
  * { box-sizing: border-box; margin: 0; padding: 0; }
  html, body {
    width: 900px; height: 1200px; overflow: hidden;
    background: var(--backdrop);
  }
  .canvas { position: relative; width: 900px; height: 1200px; }

  .card {
    position: absolute; left: 80px; width: 742px; height: 441px;
    border-radius: 22px;
    box-shadow: 0 6px 18px rgba(0,0,0,0.18);
  }
  .card--front { top: 131px; background: var(--card-front); color: var(--ink); }
  .card--back  { top: 638px; background: var(--card-back); }

  .company-title {
    position: absolute; left: 24px; top: 54px;
    font-family: "Bebas Neue", "Oswald", sans-serif;
    font-size: 43px; letter-spacing: 1.5px; line-height: 1;
    color: var(--ink);
  }
  .person { position: absolute; right: 35px; top: 48px; text-align: right; }
  .person__name {
    font-family: "Montserrat", sans-serif; font-weight: 700;
    font-size: 25px; line-height: 1.1; color: var(--ink);
  }
  .person__role {
    font-family: "Montserrat", sans-serif; font-weight: 400;
    font-size: 15.5px; margin-top: 4px; color: var(--ink-soft);
  }

  .address {
    position: absolute; left: 35px; top: 234px;
    font-family: "Montserrat", sans-serif; font-size: 15.5px; line-height: 20px;
    color: var(--ink);
  }
  .contacts {
    position: absolute; left: 37px; top: 316px; list-style: none;
    font-family: "Montserrat", sans-serif; font-size: 15.5px; color: var(--ink);
  }
  .contacts li { display: flex; align-items: center; height: 30px; }
  .contacts svg { width: 16px; height: 16px; margin-right: 10px; fill: var(--ink); }

  .brand-mark {
    position: absolute; display: flex; align-items: center;
    font-family: "Bebas Neue", "Oswald", sans-serif; line-height: 1; white-space: nowrap;
  }
  .brand-mark__square { display: inline-block; }
  .card--front .brand-mark {
    right: 36px; bottom: 62px; font-size: 38px; letter-spacing: 1px; color: var(--ink);
  }
  .card--front .brand-mark__square {
    width: 26px; height: 26px; background: var(--ink); margin-right: 12px;
  }
  .card--back .brand-mark {
    left: 50%; top: 50%; transform: translate(-50%, -50%);
    font-size: 58px; letter-spacing: 2px; color: var(--back-mark);
  }
  .card--back .brand-mark__square {
    width: 40px; height: 40px; background: var(--back-mark); margin-right: 18px;
  }
</style>
</head>
<body>
<div class="canvas">

  <section class="card card--front">
    <h1 class="company-title">CEDAR RIDGE MECHANICAL</h1>

    <div class="person">
      <p class="person__name">Daniel Ross</p>
      <p class="person__role">Managing Director</p>
    </div>

    <p class="address">418 Cedar Hollow Lane<br>Bellingham, WA 98226</p>

    <ul class="contacts">
      <li>
        <svg viewBox="0 0 24 24" aria-hidden="true"><path d="M6.6 10.8a15.1 15.1 0 0 0 6.6 6.6l2.2-2.2a1 1 0 0 1 1-.25 11.4 11.4 0 0 0 3.6.57 1 1 0 0 1 1 1V20a1 1 0 0 1-1 1A17 17 0 0 1 3 4a1 1 0 0 1 1-1h3.5a1 1 0 0 1 1 1c0 1.25.2 2.45.57 3.57a1 1 0 0 1-.25 1z"/></svg>
        555.204.7316
      </li>
      <li>
        <svg viewBox="0 0 24 24" aria-hidden="true"><path d="M2 5h20v14H2z M3.5 6.5 12 12.5l8.5-6z" fill-rule="evenodd"/></svg>
        info@cedarridgemechanical.com
      </li>
      <li>
        <svg viewBox="0 0 24 24" aria-hidden="true"><path d="M12 2a10 10 0 1 0 0 20 10 10 0 0 0 0-20zm6.9 6h-3a15 15 0 0 0-1.4-3.9A8 8 0 0 1 18.9 8zM12 4c.8 1.2 1.5 2.5 1.9 4h-3.8c.4-1.5 1.1-2.8 1.9-4zM4.3 14a8 8 0 0 1 0-4h3.4a16 16 0 0 0 0 4zm.8 2h3a15 15 0 0 0 1.4 3.9A8 8 0 0 1 5.1 16zm3-8h-3a8 8 0 0 1 4.4-3.9A15 15 0 0 0 8.1 8zM12 20c-.8-1.2-1.5-2.5-1.9-4h3.8c-.4 1.5-1.1 2.8-1.9 4zm2.3-6H9.7a14 14 0 0 1 0-4h4.6a14 14 0 0 1 0 4zm.2 5.9a15 15 0 0 0 1.4-3.9h3a8 8 0 0 1-4.4 3.9zm1.8-5.9a16 16 0 0 0 0-4h3.4a8 8 0 0 1 0 4z"/></svg>
        www.cedarridgemechanical.com
      </li>
    </ul>

    <div class="brand-mark"><span class="brand-mark__square"></span>Cedar Ridge Mechanical</div>
  </section>

  <section class="card card--back">
    <div class="brand-mark"><span class="brand-mark__square"></span>Cedar Ridge Mechanical</div>
  </section>

</div>
</body>
</html>
```